Course Lantern

CourseLantern.example will be a place for people looking for information, resources, and advisement to start or continue their education. We want a friendly, inviting site design that makes finding what potential students are looking for simple and easy to navigate. We are not committed to the colors of the logo, so variations on the color scheme are welcome.

Text instructions based on the wireframe: For the site's homepage we'd like a banner at the very top for our Logo and white space to the right of it. See attachments for logo + wireframe. Below that would be navigation. Below that split into 2/3 on the left we would have home page content, and 1/3 on the right we would have the lead form. At the bottom of the page we would have a space for types of degrees, then a footer with copyright info + site info.

See wireframes for additional page layouts.

Industry/Entity Type

Education

Requirements
Must have
• At minimum we are looking for three pages: homepage, choose your degree path page, and content page.
Nice to have
• -White space is appreciated
-Variations on the color scheme are welcome, we are not married to the existing logo's color scheme.

```html
<!DOCTYPE html>
<html lang="en">
<head>
<meta charset="utf-8">
<title>Course Lantern — Home</title>
<link rel="stylesheet" href="https://fonts.googleapis.com/css2?family=Ubuntu:ital,wght@0,400;0,500;0,700;1,400;1,500;1,700&display=swap">
<style>
:root{
  --teal:#1d4b5b;
  --teal-deep:#123a48;
  --orange:#ef7420;
  --paper:#e7e2d8;
  --ink:#3a3a3a;
  --white:#ffffff;
}
*{box-sizing:border-box;margin:0;padding:0}
html,body{width:1200px;height:1164px;overflow:hidden;background:var(--white);font-family:"Ubuntu",sans-serif;color:var(--ink)}
.page{position:relative;width:1200px;height:1164px}
.abs{position:absolute}

/* header */
.brand{left:147px;top:48px;display:flex;align-items:center;gap:12px}
.brand-mark{width:22px;height:22px;background:var(--orange)}
.brand-name{font-size:48px;font-weight:700;color:var(--teal);letter-spacing:-1px;line-height:1}
.contact{right:148px;top:46px;text-align:right;font-weight:700;font-size:14px;color:var(--teal);line-height:25px}
.contact .val{color:var(--orange);font-weight:400;font-size:19px;margin-left:4px}
.contact .mail{font-style:italic;text-decoration:underline}

/* sheet */
.sheet{left:138px;top:118px;width:924px;height:986px;background:var(--paper);box-shadow:0 0 6px rgba(0,0,0,.25)}

/* nav */
.nav{left:138px;top:130px;width:924px;height:58px;border-top:3px double var(--teal);border-bottom:3px double var(--teal);display:flex;align-items:center}
.nav a{flex:1;text-align:center;font-size:14px;font-weight:500;text-decoration:none;color:var(--orange);border-left:2px solid var(--teal);line-height:38px}
.nav a:first-child{border-left:0;color:var(--teal)}

/* hero */
.hero{left:0;top:198px;width:1200px;height:278px;background:linear-gradient(100deg,#6d5a45 0%,#8a7258 30%,#7a6a5a 55%,#9c8a70 75%,#5d4d3e 100%)}
.tile{left:168px;width:242px;height:82px;background:rgba(120,120,120,.82);border:2px solid #e8e8e8}
.tile h2{position:absolute;left:29px;top:12px;font-size:22px;line-height:26px;font-weight:500;color:var(--white);font-variant:small-caps;white-space:nowrap;text-shadow:1px 1px 1px rgba(0,0,0,.6)}
.tile .bar{position:absolute;left:18px;top:46px;width:203px;height:26px;background:linear-gradient(#fff,#d8d8d8);display:flex;align-items:center;justify-content:space-between;padding:0 8px 0 10px;font-size:14px;font-weight:700;font-style:italic;color:#222}

/* welcome */
.h-section{font-size:23px;font-weight:500;font-style:italic;color:var(--teal)}
.rule{height:4px;border-top:1px solid var(--teal);border-bottom:2px solid var(--teal)}
.copy{font-size:12px;line-height:14.6px;text-align:justify;color:#3c3c3c}
.copy p{margin-bottom:14px}
.divider{left:665px;top:493px;width:1px;height:592px;background:#7a7065}

/* degree types */
.deg-photo{top:875px;width:221px;height:83px}
.deg h3{font-size:18px;font-weight:500;font-style:italic;color:var(--teal);margin-bottom:8px}
.deg p{font-size:12px;line-height:14.5px;margin-bottom:14px}

/* form */
.intro{font-size:12px;font-style:italic;line-height:14.5px}
.lead{left:696px;top:620px;width:336px;height:460px;background:var(--teal-deep);padding:22px 17px 0 15px;color:var(--white)}
.lead label{display:block;font-size:11px;line-height:17px}
.field{height:21px;background:var(--white);border:1px solid #c8c8c8;font-size:11px;font-style:italic;color:#aaa;padding:3px 9px;margin-bottom:3px;position:relative}
.field.select::after{content:"";position:absolute;right:0;top:0;width:20px;height:19px;background:#ccc}
.field.select::before{content:"";position:absolute;right:6px;top:8px;border:4px solid transparent;border-top-color:#888;z-index:1}
.row{display:flex;gap:5px}
.btn{display:inline-block;margin-top:7px;background:var(--orange);border:1px solid #f9a45e;color:var(--white);font-size:14px;line-height:16px;padding:7px 9px}
.req{font-size:12px;margin-top:7px}

/* footer */
.foot{left:0;top:1117px;width:1200px;text-align:center;font-size:11px;line-height:15px;color:#222}
</style>
</head>
<body>
<div class="page">
  <header>
    <div class="abs brand"><span class="brand-mark"></span><span class="brand-name">Course Lantern</span></div>
    <div class="abs contact">
      <div>Call: <span class="val">555-010-2040</span></div>
      <div>Email: <span class="val mail">info@courselantern.example</span></div>
    </div>
  </header>

  <div class="abs sheet"></div>

  <nav class="abs nav">
    <a href="#">About Us</a><a href="#">Contact Us</a><a href="#">Privacy Policy</a><a href="#">Terms of Use</a><a href="#">Feed Back</a>
  </nav>

  <section class="abs hero" role="img" aria-label="Photo of a large group of students seated in a lecture hall"></section>
  <a class="abs tile" style="top:208px"><h2>What We Believe</h2><span class="bar">Our Staement Of Faith <svg width="20" height="8"><path d="M0 4h18M14 1l4 3-4 3" stroke="#222" fill="none"/></svg></span></a>
  <a class="abs tile" style="top:296px"><h2>Degree Programe</h2><span class="bar">Degree Worksheets <svg width="20" height="8"><path d="M0 4h18M14 1l4 3-4 3" stroke="#222" fill="none"/></svg></span></a>
  <a class="abs tile" style="top:384px"><h2>Visiting Campus</h2><span class="bar">Customized Visit <svg width="20" height="8"><path d="M0 4h18M14 1l4 3-4 3" stroke="#222" fill="none"/></svg></span></a>

  <section class="abs" style="left:168px;top:500px;width:467px">
    <h1 class="h-section">Welcome to Course Lantern</h1>
    <div class="rule" style="margin:9px 0 12px"></div>
    <div class="copy">
      <p>The Neighbourhoods Forward Programme is a long term plan for improving the living conditions and prospects for people in the most disadvantaged communities in Wales. The programme ensures that the money and support available from the Regional Assembly Government and various other publicly funded agencies are targeted at the poorest areas Our role is to coordinate community led regeneration of the area with local residents, through Valley Ridge Partnership Board, seeking cooperation from other organisations within the public, private and voluntary sector to work together with us to tackle many issues that affect the lives of people who live in the area.</p>
      <p>Local transport, access to relevant health care, activities for children and young people, services for the elderly, family support, the environment, education and training opportunities are just some of the issues that have been brought to the attention of Neighbourhoods Forward of which we are all working on at present.</p>
      <p>he Neighbourhoods Forward Programme is a long term plan for improving the living conditions and prospects for people in the most disadvantaged communities in Wales. The programme ensures that the money and support available from the Regional Assembly Government and various other publicly funded agencies are targeted at the poorest areas Our role is to coordinate community led regeneration of the area with local residents, through Valley Ridge.</p>
    </div>
  </section>
  <div class="abs rule" style="left:168px;top:856px;width:467px"></div>

  <div class="abs deg-photo" style="left:168px;background:linear-gradient(135deg,#2a2a2a,#6b5044 50%,#1e1e1e)" role="img" aria-label="Photo of smiling graduates in caps"></div>
  <div class="abs deg-photo" style="left:416px;background:linear-gradient(90deg,#5a3a2e,#2b2b2b 40%,#8a2a3a 70%,#7a5a48)" role="img" aria-label="Photo of faculty in academic robes"></div>
  <div class="abs deg" style="left:168px;top:970px;width:225px">
    <h3>Degree Type 1</h3>
    <p>Are you overwhelmed by the thought of choosing the right college?</p>
    <p>CourseLantern helps simplify this process by matching colleges to you and your needs.</p>
  </div>
  <div class="abs deg" style="left:416px;top:970px;width:225px">
    <h3>Degree Type 2</h3>
    <p>Are you overwhelmed by the thought of choosing the right college?</p>
    <p>CourseLantern helps simplify this process by matching colleges to you and your needs.</p>
  </div>

  <div class="abs divider"></div>

  <section class="abs" style="left:696px;top:500px;width:336px">
    <h2 class="h-section">Tell us more about YOU!</h2>
    <div class="rule" style="margin:9px 0 12px"></div>
    <p class="intro">CourseLantern provides you with accredited school information that match your interests.</p>
    <p class="intro" style="margin-top:14px">Get matched to the right schools today.</p>
    <div style="border-top:1px solid #7a7065;margin-top:10px"></div>
  </section>

  <form class="abs lead">
    <label>Subject*</label><div class="field select">Choose One</div>
    <label>Degree Level*</label><div class="field select">Choose One</div>
    <label>High School Grad Yr.*</label><div class="field select">Choose One</div>
    <label>First Name*</label><div class="field">Enter First Name</div>
    <label>Last Name*</label><div class="field">Enter Last Name</div>
    <label>Street Address*</label><div class="field">Enter Street Address</div>
    <label>Zip / City / State*</label>
    <div class="row"><div class="field" style="width:75px"></div><div class="field" style="width:130px"></div><div class="field" style="width:89px"></div></div>
    <label>Phone Number*</label><div class="field">(&nbsp;&nbsp;&nbsp;&nbsp;)</div>
    <label>Email Address*</label><div class="field">Email Address</div>
    <span class="btn">Request Information</span>
    <p class="req">*Required fields</p>
  </form>

  <footer class="abs foot">
    <div>About us &nbsp;|&nbsp; Contact Us &nbsp;|&nbsp; Privacy Policy &nbsp;|&nbsp; Terms of Use &nbsp;|&nbsp; Feed back</div>
    <div>Copyright © 2012. Course Lantern. All Rights Reserved</div>
  </footer>
</div>
</body>
</html>
```